Modern Business Card

Modern professional business card with more than just logo and demographic info. Something memorable.

We are a trendy/modern chiropractic group with an emphasis on neurology, hence the minimalist-type brain logo. We want to convey that modern and technical aspect with professionalism and the elite nature of our practice environment.

```html
<!DOCTYPE html>
<html lang="en">
<head>
<meta charset="utf-8">
<title>Kestrel Chiropractic – Business Card</title>
<link href="https://fonts.googleapis.com/css2?family=Lato:wght@300;400;700&display=swap" rel="stylesheet">
<style>
  :root {
    --backdrop: #d6d6d9;
    --card: #ffffff;
    --edge-blue: #4a80c4;
    --icon-blue: #4f7fbf;
    --ink: #111111;
    --text: #4a4a4a;
    --rule: #8a8a8a;
  }
  html, body {
    margin: 0;
    padding: 0;
    width: 1049px;
    height: 1200px;
    overflow: hidden;
    background: var(--backdrop);
    font-family: "Lato", sans-serif;
  }
  .canvas { position: relative; width: 1049px; height: 1200px; }
  .card {
    position: absolute;
    left: 175px;
    width: 699px;
    height: 399px;
    box-sizing: border-box;
    background: var(--card);
    border: 2px solid var(--edge-blue);
    box-shadow: 2px 3px 4px rgba(0,0,0,0.35);
  }
  .card--front { top: 159px; border-radius: 32px 0 32px 0; }
  .card--back  { top: 642px; border-radius: 0 32px 0 32px; }

  .v-rule { position: absolute; left: 67px; width: 1px; background: var(--rule); }
  .h-rule { position: absolute; left: 22px; width: 284px; height: 1px; background: var(--rule); }

  .icon { position: absolute; fill: none; stroke: var(--icon-blue); stroke-width: 1.3; }

  .line {
    position: absolute;
    left: 81px;
    margin: 0;
    color: var(--text);
    font-size: 19px;
    line-height: 1.2;
    white-space: nowrap;
  }
  .name { font-size: 28px; color: var(--ink); font-weight: 700; letter-spacing: -0.4px; }
  .name .surname { font-weight: 300; }
  .role { font-size: 22px; }

  .brand {
    position: absolute;
    display: flex;
    align-items: center;
    gap: 12px;
  }
  .brand__dot { border-radius: 50%; background: var(--icon-blue); flex: none; }
  .brand__name {
    font-family: "Lato", sans-serif;
    font-weight: 700;
    color: var(--ink);
    text-transform: uppercase;
    line-height: 1.05;
    letter-spacing: 1px;
  }
  .brand--front { left: 378px; top: 170px; }
  .brand--front .brand__dot { width: 46px; height: 46px; }
  .brand--front .brand__name { font-size: 25px; }
  .brand--back { left: 208px; top: 138px; gap: 18px; }
  .brand--back .brand__dot { width: 72px; height: 72px; }
  .brand--back .brand__name { font-size: 40px; }

  .url--back { font-size: 22px; }
</style>
</head>
<body>
<main class="canvas">

  <section class="card card--front" aria-label="Business card front">
    <div class="v-rule" style="top:60px;height:276px"></div>
    <div class="h-rule" style="top:127px"></div>
    <div class="h-rule" style="top:269px"></div>

    <svg class="icon" style="left:22px;top:83px" width="32" height="32" viewBox="0 0 34 34" aria-hidden="true">
      <circle cx="17" cy="11" r="8"/>
      <path d="M2 33 C2 24 8 20 17 20 C26 20 32 24 32 33 Z"/>
    </svg>
    <svg class="icon" style="left:24px;top:141px" width="30" height="26" viewBox="0 0 30 26" aria-hidden="true">
      <path d="M2 9 C2 3 28 3 28 9 L24 10 L22 7 L8 7 L6 10 Z"/>
      <path d="M8 10 L5 24 L25 24 L22 10 Z"/>
      <circle cx="15" cy="17" r="3.5"/>
    </svg>
    <svg class="icon" style="left:25px;top:230px" width="28" height="28" viewBox="0 0 28 28" aria-hidden="true">
      <circle cx="14" cy="14" r="12.5"/>
      <ellipse cx="14" cy="14" rx="5.5" ry="12.5"/>
      <path d="M1.5 14 H26.5 M3.5 8 H24.5 M3.5 20 H24.5 M14 1.5 V26.5"/>
    </svg>
    <svg class="icon" style="left:28px;top:285px" width="24" height="34" viewBox="0 0 24 34" aria-hidden="true">
      <path d="M12 32 C6 22 1.5 17 1.5 11.5 A10.5 10.5 0 0 1 22.5 11.5 C22.5 17 18 22 12 32 Z"/>
      <circle cx="12" cy="11" r="4"/>
    </svg>

    <p class="line name" style="top:64px">DR. JORDAN <span class="surname">HALE</span></p>
    <p class="line role" style="top:93px">Chiropractic</p>
    <p class="line" style="top:135px">(555) 014-2290</p>
    <p class="line" style="top:155px">(555) 014-2290</p>
    <p class="line" style="top:221px">jordan@kestrelchiro.com</p>
    <p class="line" style="top:240px">www.kestrelchiro.com</p>
    <p class="line" style="top:278px">2740 Alder Ridge Rd, Fairview,</p>
    <p class="line" style="top:300px">Ohio 45000, United State</p>

    <div class="brand brand--front">
      <span class="brand__dot"></span>
      <span class="brand__name">Kestrel<br>Chiropractic</span>
    </div>
  </section>

  <section class="card card--back" aria-label="Business card back">
    <div class="brand brand--back">
      <span class="brand__dot"></span>
      <span class="brand__name">Kestrel<br>Chiropractic</span>
    </div>

    <div class="v-rule" style="top:151px;height:220px"></div>
    <div class="h-rule" style="top:361px"></div>
    <svg class="icon" style="left:36px;top:334px" width="16" height="16" viewBox="0 0 28 28" aria-hidden="true">
      <circle cx="14" cy="14" r="12.5"/>
      <ellipse cx="14" cy="14" rx="5.5" ry="12.5"/>
      <path d="M1.5 14 H26.5 M3.5 8 H24.5 M3.5 20 H24.5 M14 1.5 V26.5"/>
    </svg>
    <p class="line url--back" style="top:327px">www.kestrelchiro.com</p>
  </section>

</main>
</body>
</html>
```